Property Services Company Needs a Brochure Design

Looking for a new brochure design for an existing property services company.

We provide a range of property services from, market research, real estate brokerage, valuation and appraisal, property development and other real estate consulting services.

We would like a fresh modern brochure design with good graphics and features. Our colours are white, blue and orange.

The design should communicate, attention to detail, superior service delivery and distinction in results.
Updates

I would like the brochure to be roughly about 20 pages.

Containing the following,

1) An introduction
2) Contents Page
2) What we do
3) Our Services
4) Agency & Brokerage
5) Real Estate Consulting
6) Market Research
7) Appraisal & Valuation
8) Project Management
9) Property Development

I would also like icons to represent items 4,5,6,7,8 & 9, they should be represented vertically on each of the pages from the contents page and highlighted individually on the pages that they represent.. i.e. on appraisal & valuation page, all six icons will be arranged vertically and the appraisal and valuations icon will be highlighted.

I will also like to have images that depict the services on the various pages.

I have some pages I think will flow which I will upload shortly.

Industry/Entity Type

Real Estate

Font styles to use
Serif

Colors
f78f20
0455a3

```html
<!DOCTYPE html>
<html lang="en">
<head>
<meta charset="utf-8">
<title>Marwick Property Services – Brochure Cover</title>
<link href="https://fonts.googleapis.com/css2?family=Arimo:wght@400&family=PT+Sans:wght@400&display=swap" rel="stylesheet">
<style>
  :root {
    --navy: #2a2160;
    --orange: #e05a12;
    --ink: #1e1e1e;
    --ink-soft: #3a3a3a;
    --paper: #ffffff;
    --frame: #9a9a9a;
    --ceiling: #f3f1ee;
    --wall-grey: #d9d6cf;
    --window: #bfc6c9;
    --stone: #d2c2a4;
    --stone-deep: #a8957a;
    --wood-dark: #4a382c;
    --floor: #cbbb9f;
    --floor-shine: #e2d7c3;
  }
  * { margin: 0; padding: 0; box-sizing: border-box; }
  html, body { width: 1200px; height: 864px; overflow: hidden; background: var(--paper); }
  .canvas {
    position: relative; width: 1200px; height: 864px;
    background: var(--paper); border: 1px solid var(--frame);
  }
  .spread {
    position: absolute; left: 40px; top: 36px; width: 1118px; height: 793px;
    border: 1px solid var(--frame); background: var(--paper); overflow: hidden;
  }
  .back-panel { position: absolute; left: 0; top: 0; width: 370px; height: 709px; background: var(--paper); }

  .lobby-photo {
    position: absolute; left: 370px; top: 0; width: 748px; height: 709px;
    background:
      radial-gradient(ellipse 150px 80px at 310px 330px, rgba(74,56,44,0.85), rgba(74,56,44,0) 100%),
      radial-gradient(ellipse 110px 140px at 620px 300px, rgba(40,34,30,0.55), rgba(40,34,30,0) 100%),
      radial-gradient(ellipse 120px 260px at 80px 320px, rgba(191,198,201,0.8), rgba(191,198,201,0) 100%),
      radial-gradient(ellipse 260px 90px at 300px 60px, rgba(255,255,255,0.95), rgba(255,255,255,0) 100%),
      radial-gradient(ellipse 300px 120px at 380px 560px, rgba(226,215,195,0.7), rgba(226,215,195,0) 100%),
      linear-gradient(90deg, rgba(168,149,122,0.35) 0%, rgba(168,149,122,0) 20%, rgba(168,149,122,0) 75%, rgba(168,149,122,0.45) 100%),
      linear-gradient(180deg, var(--ceiling) 0%, var(--ceiling) 16%, var(--wall-grey) 26%, var(--stone) 45%, var(--stone-deep) 60%, var(--floor) 66%, var(--floor-shine) 78%, var(--floor) 100%);
  }

  .fold-line { position: absolute; left: 559px; top: 0; width: 1px; height: 793px; background: rgba(90,90,90,0.55); }
  .band { position: absolute; top: 709px; height: 84px; }
  .band--navy { left: 0; width: 560px; background: var(--navy); }
  .band--orange { left: 560px; width: 558px; background: var(--orange); }

  .brand { position: absolute; display: flex; align-items: center; gap: 10px; font-family: "PT Sans", sans-serif; color: var(--ink-soft); }
  .brand__mark { background: var(--orange); flex: none; }
  .brand__text { display: flex; flex-direction: column; line-height: 1; }
  .brand--back { left: 108px; top: 556px; }
  .brand--back .brand__mark { width: 26px; height: 26px; }
  .brand--back .brand__name { font-size: 30px; }
  .brand--back .brand__tag { font-size: 12px; margin-top: 4px; }
  .brand--front { left: 728px; top: 552px; }
  .brand--front .brand__mark { width: 36px; height: 36px; }
  .brand--front .brand__name { font-size: 42px; color: #333; }
  .brand--front .brand__tag { font-size: 16px; margin-top: 5px; color: #333; }

  .contact {
    position: absolute; left: 0; width: 370px; top: 630px;
    font-family: "Arimo", sans-serif; font-size: 13px; color: var(--ink);
    text-align: center; line-height: 16px; font-style: normal;
  }
  .contact__line { display: flex; justify-content: center; align-items: center; gap: 4px; }
  .contact__line--indent { padding-left: 26px; }
  .icon { width: 12px; height: 12px; flex: none; }
  .icon--orange { fill: var(--orange); }
  .icon--navy { fill: var(--navy); }
  .gap { width: 6px; }
</style>
</head>
<body>
<main class="canvas">
  <section class="spread">
    <div class="back-panel"></div>
    <div class="lobby-photo" role="img" aria-label="Photograph of a bright modern office lobby with a lit ceiling, polished stone floor, dark wood reception wall, stone columns, glass entrance and white lounge chairs"></div>
    <div class="fold-line"></div>
    <div class="band band--navy"></div>
    <div class="band band--orange"></div>

    <div class="brand brand--back">
      <span class="brand__mark"></span>
      <span class="brand__text"><span class="brand__name">Marwick</span><span class="brand__tag">Property Services</span></span>
    </div>

    <address class="contact">
      <div class="contact__line">
        <svg class="icon icon--orange" viewBox="0 0 12 12"><path d="M6 0a4 4 0 0 0-4 4c0 3 4 8 4 8s4-5 4-8a4 4 0 0 0-4-4zm0 5.5a1.5 1.5 0 1 1 0-3 1.5 1.5 0 0 1 0 3z"/></svg>
        <span>9th floor, CEDAR COURT, 58, Marina Road</span>
      </div>
      <div class="contact__line"><span>Lagos, Nigeria</span></div>
      <div class="contact__line contact__line--indent">
        <svg class="icon icon--orange" viewBox="0 0 12 12"><path d="M3 1l2 2.5-1 1.2a6 6 0 0 0 3.3 3.3l1.2-1L11 9l-1 2C5 11 1 7 1 2z"/></svg>
        <span>+234 1 5550182</span><span class="gap"></span>
        <svg class="icon icon--orange" viewBox="0 0 12 12"><path d="M3 1l2 2.5-1 1.2a6 6 0 0 0 3.3 3.3l1.2-1L11 9l-1 2C5 11 1 7 1 2z"/></svg>
        <span>+234 1 5550247</span>
      </div>
      <div class="contact__line">
        <svg class="icon icon--navy" viewBox="0 0 12 12"><path d="M0 2h12v8H0z M0 2l6 4 6-4" fill-rule="evenodd"/></svg>
        <span>info@marwick.com.ng</span><span class="gap"></span>
        <svg class="icon icon--navy" viewBox="0 0 12 12"><circle cx="6" cy="6" r="5.5"/><path d="M0.5 6h11M6 0.5v11" stroke="#fff" stroke-width="0.8"/></svg>
        <span>www.marwick.com.ng</span>
      </div>
    </address>

    <div class="brand brand--front">
      <span class="brand__mark"></span>
      <span class="brand__text"><span class="brand__name">Marwick</span><span class="brand__tag">Property Services</span></span>
    </div>
  </section>
</main>
</body>
</html>
```